Consultancy Business Card Design

We need a business card design for a new company based in singapore called KestrelOak. KestrelOak a boutique consultancy firm offering broad-based business solutions, from conception to re-invention, for ventures from new start-ups to long-running traditional businesses.
Its 2 main divisions (Food & Beverage Operations and Construction & Project Management) have access to a wide range of networks, knowledge bases, and resources to service its clients across numerous diverse sectors. This includes, and is not limited to, construction, F&B, and retail.
We are a company that combines the ambition, boldness and energy of one in the 20s with the dedication, level-headedness and dependability of one entering its 30s. Bridging the experiences of the old with ideals of the young, we draw on the positives of both to create a unique synergy.
We hope to see designs that fits our company profile.
Industry/Entity Type
Boutique
Contact Information for Business Card
KestrelOak(Company Name)
Marcus Thiel (Name)
Principle Consultant (Title)
F&B and Hospitality (Division)
(+65) 8043 5617 (Contact no.)
marcus@kestreloak.com.sg (Email)
Colors
Designer to choose colors to be used in the design.

```html
<!DOCTYPE html>
<html lang="en">
<head>
<meta charset="utf-8">
<title>KestrelOak Business Card</title>
<link rel="stylesheet" href="https://fonts.googleapis.com/css2?family=Arimo:wght@400&display=swap">
<style>
  :root {
    --page-bg: #e4e4e4;
    --card-bg: #323231;
    --ink-light: #ffffff;
  }
  * { margin: 0; padding: 0; box-sizing: border-box; }
  html, body {
    width: 900px;
    height: 1200px;
    overflow: hidden;
  }
  body {
    position: relative;
    background: var(--page-bg);
    font-family: "Arimo", Arial, sans-serif;
    color: var(--ink-light);
  }
  .card {
    position: absolute;
    left: 154px;
    width: 562px;
    height: 346px;
    background: var(--card-bg);
  }
  .card--front { top: 185px; }
  .card--back { top: 689px; }

  .wordmark {
    position: absolute;
    font-weight: 400;
    line-height: 1;
    letter-spacing: -0.5px;
    white-space: nowrap;
  }
  .card--front .wordmark {
    left: 0;
    right: 0;
    top: 137px;
    text-align: center;
    font-size: 56px;
  }
  .card--back .wordmark {
    left: 48px;
    top: 62px;
    font-size: 44px;
  }

  .contact {
    position: absolute;
    left: 371px;
    top: 204px;
    white-space: nowrap;
  }
  .contact__name {
    font-size: 17px;
    line-height: 20px;
  }
  .contact__title {
    font-size: 8px;
    line-height: 10px;
    margin-top: 4px;
  }
  .contact__details {
    list-style: none;
    margin-top: 11px;
    font-size: 11px;
    line-height: 19px;
  }
</style>
</head>
<body>
  <section class="card card--front" aria-label="Card front">
    <div class="wordmark">KestrelOak</div>
  </section>

  <section class="card card--back" aria-label="Card back">
    <div class="wordmark">KestrelOak</div>
    <div class="contact">
      <p class="contact__name">Marcus Thiel</p>
      <p class="contact__title">Principle Consultant</p>
      <ul class="contact__details">
        <li>F&amp;B and Hospitality</li>
        <li>(+65) 8043 5617</li>
        <li>marcus@kestreloak.com.sg</li>
      </ul>
    </div>
  </section>
</body>
</html>
```